Build a landing page to promote a service (dialler consultation and support).

We are a call centre consultation firm and we need a landing page to promote a service. The service is Tormalux dialler consultation and support.
If you do not know what Tormalux is, please do some quick "Zorvex" research for more information.
The landing page will be promoted with a paid advertisement, so we want something that is simple, and explains exactly what service we offer.
There are two objectives for the landing page:
1) A "call to action" which directs the user to a contact page, including a form plus all of our contact details.
2) A form for them viewers to enter their details to get a "FREE" quote for their project. This form should be placed on the main page.
Notes:
The call to action will require the viewer to enter their name, email, phone number as well as a description of their request. There will also need to be a drop down menu for the type of quote. This menu should have the following options:
1) Tormalux support
2) Tormalux hosting
3) Tormalux customisation
4) Other
We need 2 pages in total:
1) Main landing page
This is the home page. It will need to clearly indicate our services and our key selling features.
Services:
* Tormalux support
* Tormalux hosting
* Tormalux customisation
Key Selling Features:
* Australian based
* PCI complaint
* 10+ years of dialler and call centre experience
* we run a sister company which is a highly reputable 40 seat call centre, so we know first hand about call centre technology.
The main landing page will have an "about us" section with a few paragraphs about how we got started.
-------------------------------------------------------------------------
2) Contact page
All of our contact details will live on this page, as well as a contact form.
Other notes:
We will be self hosting the landing page.
We already have a domain name.
The design must be clean and incorporate our logo, as well as it's colours. (Logo attached)
We want a fully function HTML landing page, not just a "PSD" design.
The page must be mobile optimised.
Anyone using Tormalux software.

```html
<!DOCTYPE html>
<html lang="en">
<head>
<meta charset="utf-8">
<title>Harbourline – Tormalux Support</title>
<link href="https://fonts.googleapis.com/css2?family=Lato:wght@400;700;900&display=swap" rel="stylesheet">
<style>
:root{
  --teal:#1d9cbf;
  --teal-dark:#14809f;
  --blue:#2b8ccb;
  --ink:#333a40;
  --muted:#6d757b;
  --line:#d3d8dc;
  --soft:#eff2f4;
  --footer:#2a2c2e;
  --white:#ffffff;
}
*{box-sizing:border-box;margin:0;padding:0}
html,body{width:1200px;height:3452px;overflow:hidden;background:var(--white);font-family:'Lato',sans-serif;color:var(--ink)}
.canvas{position:relative;width:1200px;height:3452px}
.abs{position:absolute}

/* header */
.site-header{position:absolute;left:0;width:1200px;height:136px;background:var(--white)}
.brand{position:absolute;left:70px;top:44px;font-size:32px;font-weight:700;color:var(--ink);line-height:1}
.main-nav{position:absolute;right:60px;top:52px;display:flex;gap:34px;font-size:15px;font-weight:700;color:var(--ink)}
.main-nav .active{color:var(--teal)}
.dropdown{position:absolute;left:790px;top:90px;width:170px;background:var(--teal);padding:8px 0;z-index:3}
.dropdown li{list-style:none;color:var(--white);font-size:12px;padding:5px 14px;border-bottom:1px solid rgba(255,255,255,.2);white-space:nowrap}
.dropdown li:last-child{border:none}

/* hero */
.hero{top:136px;left:0;width:1200px;height:576px;background:linear-gradient(110deg,#8fa4b4 0%,#cdd6dd 40%,#e3e8ec 65%,#b9c5ce 100%)}
.hero-title{position:absolute;left:70px;top:348px;font-size:40px;font-weight:900;color:var(--white)}
.hero-text{position:absolute;left:70px;top:400px;width:500px;font-size:20px;line-height:1.35;color:var(--white);font-weight:700}
.quote-box{position:absolute;left:700px;top:220px;width:460px;height:430px;background:var(--white);padding:18px 22px;box-shadow:0 6px 18px rgba(0,0,0,.18)}
.quote-box h2{font-size:28px;font-weight:900;color:var(--teal);margin-bottom:14px}
.field{height:34px;border:1px solid var(--line);margin-bottom:12px;font-size:12px;color:var(--muted);padding:9px 10px;position:relative}
.field.select::after{content:"";position:absolute;right:12px;top:14px;border:5px solid transparent;border-top-color:var(--ink)}
.field.area{height:60px}
.btn{display:block;background:linear-gradient(#27aacb,var(--teal-dark));color:var(--white);font-weight:700;text-align:center;text-transform:uppercase;font-size:14px;letter-spacing:.5px}
.quote-box .btn{height:48px;line-height:48px;font-size:20px;margin-top:16px}

/* services */
.section-title{font-size:44px;font-weight:700;color:var(--blue)}
.services-title{position:absolute;top:770px;width:1200px;text-align:center}
.rule{width:80px;height:2px;background:var(--line);margin:10px auto 0}
.service{position:absolute;top:870px;width:280px;text-align:center}
.service svg{display:block;margin:0 auto 18px}
.service h3{font-size:20px;font-weight:700;color:var(--teal);margin-bottom:8px}
.service p{font-size:13px;line-height:1.45;color:var(--muted)}

/* about */
.about-copy{position:absolute;left:70px;top:1210px;width:520px}
.about-copy h2{color:var(--blue);margin-bottom:18px}
.about-copy p{font-size:15px;line-height:1.55;color:var(--blue)}
.about-copy .btn,.features .btn{width:150px;height:46px;line-height:46px;margin-top:22px}
.about-photo{top:1172px;left:600px;width:600px;height:460px;background:linear-gradient(135deg,#d9dde0,#a8b2b8 60%,#7d8a92);clip-path:polygon(12% 0,100% 0,100% 100%,0 100%)}
.features-photo{top:1640px;left:0;width:600px;height:490px;background:linear-gradient(135deg,#6f7c86,#c7ced3 55%,#e7eaec);clip-path:polygon(0 0,100% 0,88% 100%,0 100%)}
.features{position:absolute;left:640px;top:1690px;width:500px}
.features h2{color:var(--blue);margin-bottom:24px}
.features li{list-style:none;display:flex;gap:12px;font-size:15px;line-height:1.45;color:var(--ink);margin-bottom:12px}
.features li svg{flex:none;margin-top:3px}

/* footer */
.site-footer{position:absolute;left:0;width:1200px;height:68px;background:var(--footer);color:#aab0b4;font-size:12px}
.site-footer .copy{position:absolute;left:70px;top:27px}
.social{position:absolute;right:70px;top:24px;display:flex;gap:14px}
.social span{width:18px;height:18px;background:#d7dadc;border-radius:3px}

/* contact page */
.contact-band{top:2448px;left:0;width:1200px;height:400px;background:var(--soft)}
.contact-info{position:absolute;left:70px;top:2540px}
.contact-info h2{color:var(--blue);margin-bottom:20px}
.contact-info li{list-style:none;display:flex;align-items:center;gap:14px;font-size:14px;color:var(--ink);margin-bottom:14px}
.map{top:2448px;left:560px;width:640px;height:400px;background:linear-gradient(160deg,#e9ece2,#d6dccf 50%,#e4e0d4)}
.quick-title{position:absolute;top:2960px;width:1200px;text-align:center}
.quick-form{position:absolute;left:205px;top:3040px;width:790px}
.row{display:flex;gap:40px}
.row .field{flex:1}
.quick-form .area{height:70px}
.quick-form .btn{width:150px;height:42px;line-height:42px;margin:20px auto 0}
</style>
</head>
<body>
<div class="canvas">

<!-- landing page -->
<header class="site-header" style="top:0">
  <div class="brand">Harbourline</div>
  <nav class="main-nav"><span class="active">HOME</span><span>ABOUT US</span><span>SERVICES ▾</span><span>FEATURES</span><span>CONTACT US</span></nav>
</header>
<ul class="dropdown">
  <li>Tormalux Support</li><li>Tormalux Hosting</li><li>Tormalux Customisation</li><li>Other</li>
</ul>

<section class="abs hero" role="img" aria-label="Photo of a smiling call centre agent wearing a headset"></section>
<h1 class="hero-title">Tormalux Support</h1>
<p class="hero-text">Praesent auctor, consectetur sit amet dignissim et, scelerisque sed lacus. Mauris facilisis mattis lectus, et pellentesque arcu ultricies vel.</p>

<form class="quote-box">
  <h2>Get A Free Quote Now</h2>
  <div class="field">Name</div>
  <div class="field">Email Address</div>
  <div class="field">Phone No</div>
  <div class="field select">Select Services</div>
  <div class="field area">Description of their request</div>
  <span class="btn">Get a free quote</span>
</form>

<div class="services-title"><h2 class="section-title">Services</h2><div class="rule"></div></div>

<div class="service" style="left:120px">
  <svg width="52" height="48" viewBox="0 0 52 48"><path d="M4 4h30a4 4 0 0 1 4 4v16a4 4 0 0 1-4 4H16l-8 7v-7H4a4 4 0 0 1-4-4V8a4 4 0 0 1 4-4z" fill="#333a40"/><path d="M42 14h6a4 4 0 0 1 4 4v14a4 4 0 0 1-4 4h-2v7l-8-7H26a4 4 0 0 1-4-4v-2h14a6 6 0 0 0 6-6z" fill="#333a40"/></svg>
  <h3>Tormalux Support</h3>
  <p>Aliquam molestie, mi et imperdiet euismod, dui purus auctor tellus, et interdum lacus...</p>
</div>
<div class="service" style="left:460px">
  <svg width="44" height="50" viewBox="0 0 44 50"><ellipse cx="22" cy="7" rx="20" ry="6" fill="#333a40"/><path d="M2 12c0 4 9 7 20 7s20-3 20-7v10c0 4-9 7-20 7S2 26 2 22z" fill="#333a40"/><path d="M2 27c0 4 9 7 20 7s20-3 20-7v10c0 4-9 7-20 7S2 41 2 37z" fill="#333a40"/></svg>
  <h3>Tormalux Hosting</h3>
  <p>Aliquam molestie, mi et imperdiet euismod, dui purus auctor tellus, et interdum lacus...</p>
</div>
<div class="service" style="left:800px">
  <svg width="48" height="48" viewBox="0 0 48 48" fill="none" stroke="#333a40" stroke-width="6"><path d="M40 18A17 17 0 0 0 9 14"/><path d="M8 30a17 17 0 0 0 31 4"/><path d="M42 6v14H28" stroke-width="5"/><path d="M6 42V28h14" stroke-width="5"/></svg>
  <h3>Tormalux Customisation</h3>
  <p>Aliquam molestie, mi et imperdiet euismod, dui purus auctor tellus, et interdum lacus...</p>
</div>

<div class="about-copy">
  <h2 class="section-title">About Us</h2>
  <p>Aliquam molestie, mi et imperdiet euismod, dui purus auctor tellus, et interdum lacus tellus et ante. Lorem ipsum dolor sit amet, consectetur adipiscing elit. Donec eu porttitor mauris. Etiam id orci facilisis, venenatis nibh id, condimentum est. Praesent arcu est, consectetur sit amet dignissim et, scelerisque sed lacus. Mauris facilisis mattis lectus, et pellentesque arcu ultricies vel. Donec id elit sollicitudin, commodo urna eget, gravida velit.</p>
  <span class="btn">Read more</span>
</div>
<div class="abs about-photo" role="img" aria-label="Photo of a team working at laptops in an office"></div>

<div class="abs features-photo" role="img" aria-label="Photo of call centre staff at their desks with a supervisor"></div>
<div class="features">
  <h2 class="section-title">Key Selling Features</h2>
  <ul>
    <li><svg width="14" height="14" viewBox="0 0 14 14"><path d="M2 7l3.5 3.5L12 3" fill="none" stroke="#1d9cbf" stroke-width="2.5"/></svg>Australian based</li>
    <li><svg width="14" height="14" viewBox="0 0 14 14"><path d="M2 7l3.5 3.5L12 3" fill="none" stroke="#1d9cbf" stroke-width="2.5"/></svg>PCI complaint</li>
    <li><svg width="14" height="14" viewBox="0 0 14 14"><path d="M2 7l3.5 3.5L12 3" fill="none" stroke="#1d9cbf" stroke-width="2.5"/></svg>10+ years of dialler and call centre experience</li>
    <li><svg width="14" height="14" viewBox="0 0 14 14"><path d="M2 7l3.5 3.5L12 3" fill="none" stroke="#1d9cbf" stroke-width="2.5"/></svg>We run a sister company which is a highly reputable 40 seat call centre, so we know first hand about call centre technology.</li>
  </ul>
  <span class="btn">Read more</span>
</div>

<footer class="site-footer" style="top:2140px">
  <span class="copy">Copyright ©2019 Harbourline. All Rights Reserved</span>
  <div class="social"><span></span><span></span><span></span><span></span><span></span></div>
</footer>

<!-- contact page -->
<header class="site-header" style="top:2312px">
  <div class="brand">Harbourline</div>
  <nav class="main-nav"><span>HOME</span><span>ABOUT US</span><span>SERVICES ▾</span><span>FEATURES</span><span class="active">CONTACT US</span></nav>
</header>

<section class="abs contact-band"></section>
<div class="abs map" role="img" aria-label="Street map showing the office location with a red pin"></div>
<div class="contact-info">
  <h2 class="section-title">Contact Us</h2>
  <ul>
    <li><svg width="14" height="18" viewBox="0 0 14 18"><path d="M7 0a7 7 0 0 1 7 7c0 5-7 11-7 11S0 12 0 7a7 7 0 0 1 7-7z" fill="#333a40"/><circle cx="7" cy="7" r="2.5" fill="#eff2f4"/></svg>14 Harbour Lane, Brightwater City, AUS</li>
    <li><svg width="16" height="16" viewBox="0 0 16 16"><path d="M3 1l3 3-2 2a10 10 0 0 0 6 6l2-2 3 3-2 2C7 15 1 9 1 3z" fill="#333a40"/></svg>1-800-555-0142</li>
    <li><svg width="16" height="16" viewBox="0 0 16 16"><rect x="1" y="4" width="14" height="9" fill="#333a40"/><rect x="4" y="1" width="8" height="4" fill="#333a40"/></svg>1-800-555-0199</li>
    <li><svg width="16" height="12" viewBox="0 0 16 12"><rect width="16" height="12" fill="#333a40"/><path d="M0 0l8 6 8-6" fill="none" stroke="#eff2f4" stroke-width="1.5"/></svg>info@harbourline-mail.com</li>
    <li><svg width="14" height="18" viewBox="0 0 14 18"><path d="M7 0a7 7 0 0 1 7 7c0 5-7 11-7 11S0 12 0 7a7 7 0 0 1 7-7z" fill="#333a40"/></svg>Map Direction</li>
  </ul>
</div>

<div class="quick-title"><h2 class="section-title">Quick Contact</h2><div class="rule"></div></div>
<form class="quick-form">
  <div class="row"><div class="field">Name</div><div class="field">Email Address</div></div>
  <div class="row"><div class="field">Phone No</div><div class="field select">Select Services</div></div>
  <div class="field area">Description</div>
  <span class="btn">Submit</span>
</form>

<footer class="site-footer" style="top:3352px">
  <span class="copy">Copyright ©2019 Harbourline. All Rights Reserved</span>
  <div class="social"><span></span><span></span><span></span><span></span><span></span></div>
</footer>

</div>
</body>
</html>
```